Letterhead, stationery and email signature for construction business

I need the letterhead, stationery and email signature designs for a construction business. I want them to have a corporate feel to them.

I've attached the logo for reference.

```html
<!DOCTYPE html>
<html lang="en">
<head>
<meta charset="utf-8">
<title>Brantwell Projects – Business Cards</title>
<link href="https://fonts.googleapis.com/css2?family=Montserrat:wght@700;800&family=Roboto:wght@400;500&display=swap" rel="stylesheet">
<style>
  :root {
    --brand-blue: #2f5aa8;
    --brand-blue-light: #4a72bd;
    --brand-slate: #4b4b5f;
    --text-grey: #5a5a66;
    --rule-grey: #8a8a94;
    --paper: #ffffff;
    --backdrop: #e4e5e8;
  }
  * { margin: 0; padding: 0; box-sizing: border-box; }
  html, body { width: 1200px; height: 904px; overflow: hidden; background: var(--backdrop); }
  .canvas { position: relative; width: 1200px; height: 904px; }

  .card {
    position: absolute; left: 280px; width: 640px; height: 366px;
    box-shadow: 0 6px 18px rgba(0,0,0,.18);
    overflow: hidden;
  }
  .card--back { top: 70px; background: var(--brand-blue); display: flex; align-items: center; justify-content: center; }
  .card--front { top: 470px; background: var(--paper); }

  .wordmark {
    font-family: "Montserrat", sans-serif; font-weight: 800;
    display: flex; align-items: center; gap: 10px;
    white-space: nowrap; line-height: 1;
  }
  .wordmark__square { flex: none; }

  .card--back .wordmark { color: var(--brand-blue-light); font-size: 30px; margin-bottom: 40px; }
  .card--back .wordmark__square { width: 30px; height: 30px; background: var(--brand-blue-light); }

  .card--front .wordmark { position: absolute; left: 44px; top: 168px; color: var(--brand-blue); font-size: 20px; }
  .card--front .wordmark__square { width: 22px; height: 22px; background: var(--brand-blue); }

  .divider { position: absolute; left: 372px; top: 46px; width: 1px; height: 220px; background: var(--rule-grey); }

  .contact { position: absolute; left: 398px; top: 50px; font-family: "Roboto", sans-serif; color: var(--text-grey); }
  .contact__name { font-family: "Montserrat", sans-serif; font-weight: 800; font-size: 20px; color: var(--brand-blue); letter-spacing: .3px; }
  .contact__title { font-family: "Montserrat", sans-serif; font-weight: 700; font-size: 15px; color: var(--text-grey); margin-top: 2px; }
  .contact__list { list-style: none; margin-top: 18px; font-size: 14.5px; line-height: 22px; }
  .contact__list li { display: flex; align-items: center; gap: 7px; }
  .contact__list svg { width: 13px; height: 13px; flex: none; }
  .contact__address { margin-top: 12px; font-size: 14.5px; line-height: 21px; }

  .bands { position: absolute; left: 0; bottom: 0; width: 640px; height: 110px; }
</style>
</head>
<body>
<div class="canvas">

  <section class="card card--back" aria-label="Card back">
    <div class="wordmark">
      <div class="wordmark__square"></div>
      <span class="wordmark__text">BRANTWELL PROJECTS</span>
    </div>
  </section>

  <section class="card card--front" aria-label="Card front">
    <div class="wordmark">
      <div class="wordmark__square"></div>
      <span class="wordmark__text">BRANTWELL PROJECTS</span>
    </div>

    <div class="divider"></div>

    <div class="contact">
      <div class="contact__name">MARTIN HALE</div>
      <div class="contact__title">President</div>
      <ul class="contact__list">
        <li>
          <svg viewBox="0 0 16 16" fill="var(--brand-blue)"><path d="M3.6 1.2l2.2 2.6-1.3 1.8c.9 2 2.5 3.6 4.6 4.6l1.8-1.3 2.6 2.2-1.3 2.4C7 13.3 2.7 9 1.2 3.6z"/></svg>
          (555) 014-2290
        </li>
        <li>
          <svg viewBox="0 0 16 16" fill="none" stroke="var(--brand-blue)" stroke-width="1.6"><rect x="1" y="3" width="14" height="10"/><path d="M1 3l7 6 7-6"/></svg>
          info@brantwell.com
        </li>
        <li>
          <svg viewBox="0 0 16 16" fill="none" stroke="var(--brand-blue)" stroke-width="1.3"><circle cx="8" cy="8" r="6.5"/><ellipse cx="8" cy="8" rx="3" ry="6.5"/><path d="M1.5 8h13M2.5 4.8h11M2.5 11.2h11"/></svg>
          www.brantwell.com
        </li>
      </ul>
      <p class="contact__address">Brantwell Project, Ltd.<br>Harlow House, 18 Fenmore<br>Ave, London SW4 7QT</p>
    </div>

    <svg class="bands" viewBox="0 0 640 110" preserveAspectRatio="none" aria-hidden="true">
      <polygon points="0,88 420,88 440,30 452,30 426,110 0,110" fill="var(--brand-blue)"/>
      <polygon points="457,30 640,30 640,44 452,44" fill="var(--brand-slate)"/>
    </svg>
  </section>

</div>
</body>
</html>
```